2021 Summer Ads Hollis Bay Custom Homes

We need a re-design of our summer ad run for our customer, Hollis Bay Custom Homes. They are custom home builders in the mostly rural parts of West Virginia, USA. They are known for their "Forever Home" tagline. We'd like two designed ads with the main difference being just the custom home that's featured. These designs should be for a Zintrola banner like 300 x 250 and square ad like 250 x 250. For inspiration please visit the Hollis Bay Custom Homes website at www dot hollisbaycustomhomes dot com

Target Market(s)

consumers / new home shoppers

Industry/Entity Type

Consumer

Requirements
Must have
• HBCH logo
Price Lock Available!
Custom home pic
Learn more >
small CFRM logo mark

```html
<!DOCTYPE html>
<html lang="en">
<head>
<meta charset="utf-8">
<title>Hollis Bay Custom Homes – Summer Ads</title>
<link rel="stylesheet" href="https://fonts.googleapis.com/css2?family=Jost:wght@400;600&family=Montserrat:wght@600;700&family=Roboto:wght@400&display=swap">
<style>
  :root {
    --board: #d9d9d9;
    --label: #6b5857;
    --ink-dark: #16161c;
    --brand-red: #e31b37;
    --deep-red: #8e0f22;
    --navy: #0e1431;
    --white: #ffffff;
  }
  html, body {
    margin: 0;
    width: 1200px;
    height: 668px;
    overflow: hidden;
    background: var(--board);
  }
  .board { position: relative; width: 1200px; height: 668px; }
  .size-label {
    position: absolute;
    margin: 0;
    font-family: "Roboto", Arial, sans-serif;
    font-weight: 400;
    font-size: 51px;
    line-height: 1;
    color: var(--label);
  }
  .size-label--square { left: 143px; top: 76px; }
  .size-label--banner { left: 530px; top: 76px; }
  .ad { position: absolute; display: block; }
  .ad--square { left: 144px; top: 147px; width: 338px; height: 338px; }
  .ad--banner { left: 532px; top: 147px; width: 507px; height: 422px; }
  .headline-light { font-family: "Jost", sans-serif; font-weight: 400; fill: var(--white); }
  .headline-bold { font-family: "Jost", sans-serif; font-weight: 600; fill: var(--white); }
  .offer { font-family: "Montserrat", sans-serif; font-weight: 700; fill: var(--white); }
  .cta-text { font-family: "Montserrat", sans-serif; font-weight: 700; fill: var(--white); letter-spacing: .3px; }
  .brand-name { font-family: "Jost", sans-serif; font-weight: 600; fill: var(--white); }
  .partner-name { font-family: "Montserrat", sans-serif; font-weight: 700; fill: var(--white); }
  .partner-sub { font-family: "Montserrat", sans-serif; font-weight: 600; fill: var(--white); }
</style>
</head>
<body>
<main class="board">

  <h2 class="size-label size-label--square">250 x 250</h2>
  <svg class="ad ad--square" viewBox="0 0 400 400" aria-label="Hollis Bay Custom Homes square ad">
    <defs>
      <linearGradient id="sq-band" x1="0" y1="0" x2="1" y2="1">
        <stop offset="0" stop-color="#e31b37"/>
        <stop offset="1" stop-color="#6e0c1a"/>
      </linearGradient>
      <linearGradient id="sq-photo" x1="0" y1="0" x2="0" y2="1">
        <stop offset="0" stop-color="#b8b4d6"/>
        <stop offset=".35" stop-color="#e9e6ea"/>
        <stop offset=".7" stop-color="#9c7b5e"/>
        <stop offset="1" stop-color="#b9a48e"/>
      </linearGradient>
    </defs>
    <rect class="ad-bg" width="400" height="400" fill="var(--ink-dark)"/>
    <polygon class="accent-corner" points="0,0 60,0 0,60" fill="url(#sq-band)"/>
    <polygon class="accent-band" points="250,0 300,0 100,388 50,400 70,388" fill="url(#sq-band)"/>
    <g role="img" aria-label="Photo of a lit two-storey custom home with stone columns and a screened porch at dusk">
      <polygon points="300,0 400,0 400,388 100,388" fill="url(#sq-photo)"/>
    </g>
    <rect class="accent-strip" x="100" y="388" width="300" height="12" fill="var(--brand-red)"/>

    <g class="brand-lockup">
      <rect x="16" y="48" width="22" height="22" fill="var(--white)"/>
      <text class="brand-name" x="46" y="67" font-size="25">Hollis Bay</text>
      <text class="headline-light" x="47" y="84" font-size="11" letter-spacing="1.5">CUSTOM HOMES</text>
    </g>

    <text class="headline-light" x="13" y="123" font-size="24">START BUILDING</text>
    <text class="headline-bold" x="13" y="152" font-size="24">YOUR FOREVER</text>
    <text class="headline-bold" x="13" y="181" font-size="24">HOME TODAY!</text>
    <text class="offer" x="11" y="208" font-size="12">PRICE LOCK AVAILABLE!</text>

    <g class="cta">
      <rect x="12" y="230" width="125" height="37" fill="var(--brand-red)"/>
      <circle cx="132" cy="248.5" r="18.5" fill="var(--deep-red)"/>
      <polyline points="129,242 135,248.5 129,255" fill="none" stroke="var(--white)" stroke-width="2.6"/>
      <text class="cta-text" x="29" y="253" font-size="11">LEARN MORE</text>
    </g>

    <g class="partner">
      <text class="partner-name" x="17" y="330" font-size="22">CFRM</text>
      <text class="partner-sub" x="17" y="343" font-size="7.5">Council for Family</text>
      <text class="partner-sub" x="17" y="352" font-size="7.5">Residence Makers</text>
    </g>
  </svg>

  <h2 class="size-label size-label--banner">300 x 250</h2>
  <svg class="ad ad--banner" viewBox="0 0 600 500" aria-label="Hollis Bay Custom Homes banner ad">
    <defs>
      <linearGradient id="bn-photo" x1="0" y1="0" x2="0" y2="1">
        <stop offset="0" stop-color="#6f9ad0"/>
        <stop offset=".2" stop-color="#dfe3e6"/>
        <stop offset=".75" stop-color="#d2d3cf"/>
        <stop offset=".82" stop-color="#5f8a3c"/>
        <stop offset="1" stop-color="#4f7a2c"/>
      </linearGradient>
      <linearGradient id="bn-panel" x1="0" y1="0" x2="0" y2="1">
        <stop offset="0" stop-color="#8e0f22" stop-opacity=".95"/>
        <stop offset="1" stop-color="#e31b37" stop-opacity=".92"/>
      </linearGradient>
    </defs>
    <g role="img" aria-label="Photo of a white farmhouse-style custom home with a metal roof and green lawn">
      <rect width="600" height="500" fill="url(#bn-photo)"/>
    </g>
    <path class="accent-arc" d="M212 0 C345 85 370 330 160 500 H140 C345 330 320 85 196 0 Z" fill="var(--brand-red)"/>
    <path class="accent-arc-white" d="M196 0 C320 85 345 330 140 500 H128 C330 330 305 85 184 0 Z" fill="var(--white)"/>
    <path class="text-panel" d="M0 0 H184 C305 85 330 330 128 500 H0 Z" fill="url(#bn-panel)"/>

    <g class="brand-lockup">
      <rect x="26" y="90" width="28" height="28" fill="var(--white)"/>
      <text class="brand-name" x="64" y="113" font-size="33">Hollis Bay</text>
      <text class="headline-light" x="65" y="133" font-size="13" letter-spacing="2">CUSTOM HOMES</text>
    </g>

    <text class="headline-light" x="23" y="175" font-size="32">START BUILDING</text>
    <text class="headline-bold" x="23" y="213" font-size="32">YOUR FOREVER</text>
    <text class="headline-bold" x="23" y="250" font-size="32">HOME TODAY!</text>
    <text class="offer" x="26" y="287" font-size="16">PRICE LOCK AVAILABLE!</text>

    <g class="cta">
      <rect x="25" y="309" width="150" height="45" rx="3" fill="var(--navy)"/>
      <circle cx="172" cy="331.5" r="17" fill="var(--brand-red)"/>
      <polyline points="168.5,324.5 175,331.5 168.5,338.5" fill="none" stroke="var(--white)" stroke-width="2.8"/>
      <text class="cta-text" x="46" y="336" font-size="13">LEARN MORE</text>
    </g>

    <g class="partner">
      <text class="partner-name" x="27" y="422" font-size="30">CFRM</text>
      <text class="partner-sub" x="27" y="436" font-size="10">Council for Family</text>
      <text class="partner-sub" x="27" y="447" font-size="10">Residence Makers</text>
    </g>
  </svg>

</main>
</body>
</html>
```